Logo for a Food & Beverage Franchise Company

We need a logo and stationary for a new company that just aquired a restaurant franchise. We need a sleep and professional logo with stationary.

Target Market(s)

Adults, resturaunt owners, franchisors (Companies who own food franchise companies such as Farrowbys Head Office, Toastwell International Franchise)
and Big Food and Beverage who wish to give franchise rights to us)

Industry/Entity Type

Restaurant

Logo Text

Velvet Harbor

Logo styles of interest
Emblem Logo
Pictorial/Combination Logo
Character Logo
Font styles to use
Serif
Sans Serif

Colors
ffc214
f78f20
f37022
faa54b
fece3e
fbed22

Requirements
Must have
• Maximum three color. The less the better.
Nice to have
• It does not have to have a crown, but if you wish to have a crown then it does not have to be so sharp and clear. Abstract is better.

```html
<!DOCTYPE html>
<html lang="en">
<head>
<meta charset="utf-8">
<title>Velvet Harbor — Stationery</title>
<link rel="stylesheet" href="https://fonts.googleapis.com/css2?family=Montserrat:wght@500;600&family=Open+Sans:wght@400;600&display=swap">
<style>
  :root {
    --bg: #56606b;
    --charcoal: #373737;
    --charcoal-soft: #4a4a4a;
    --faint: #707070;
    --orange: #f78f20;
    --paper: #ffffff;
    --ink: #2b2b2b;
    --muted: #cfcfcf;
  }
  * { box-sizing: border-box; margin: 0; padding: 0; }
  html, body { width: 1200px; height: 900px; overflow: hidden; }
  body {
    background: var(--bg);
    font-family: "Open Sans", Arial, sans-serif;
    position: relative;
  }
  .logotype {
    font-family: "Montserrat", Arial, sans-serif;
    font-weight: 600;
    letter-spacing: 0.2em;
    text-transform: uppercase;
    white-space: nowrap;
  }
  .mark-square { display: inline-block; width: 10px; height: 10px; background: currentColor; vertical-align: middle; margin-right: 8px; }

  /* Folder cover */
  .folder {
    position: absolute; left: 60px; top: 50px; width: 320px; height: 450px;
    background: var(--charcoal); overflow: hidden;
    box-shadow: 4px 4px 0 #e6e6e6;
  }
  .folder__band {
    position: absolute; left: 0; top: 0; width: 100%; height: 110px;
    background: var(--orange); color: var(--paper);
    display: flex; align-items: center; justify-content: flex-end; padding-right: 26px;
    font-size: 13px;
  }
  .folder__watermark {
    position: absolute; left: -20px; bottom: 110px; font-size: 44px; color: var(--faint);
    transform: rotate(-30deg); transform-origin: left bottom;
  }

  /* Letterhead */
  .letterhead {
    position: absolute; left: 420px; top: 50px; width: 330px; height: 450px;
    background: var(--paper); padding: 30px 30px 24px;
  }
  .letterhead__logo { color: var(--orange); font-size: 12px; text-align: right; margin-bottom: 30px; }
  .letterhead__body p {
    font-size: 8.5px; line-height: 1.55; color: var(--ink); margin-bottom: 10px; text-align: justify;
  }
  .letterhead__foot {
    position: absolute; left: 30px; bottom: 26px; width: 16px; height: 16px; background: var(--orange);
  }

  /* Business cards */
  .card {
    position: absolute; width: 200px; height: 116px; background: var(--charcoal); overflow: hidden;
  }
  .card--front { left: 800px; top: 50px; }
  .card--back { left: 800px; top: 190px; display: flex; align-items: center; justify-content: center; }
  .card__band {
    height: 28px; background: var(--orange); color: var(--paper);
    font-size: 8px; display: flex; align-items: center; padding-left: 14px;
  }
  .card__details { padding: 12px 14px; color: var(--muted); font-size: 7.5px; line-height: 1.6; }
  .card__name { color: var(--orange); font-weight: 600; font-size: 9px; }
  .card__mark { color: var(--faint); font-size: 13px; }

  /* Disc */
  .disc {
    position: absolute; left: 1010px; top: 60px; width: 150px; height: 150px; border-radius: 50%;
    background: var(--charcoal); display: flex; align-items: center; justify-content: center;
  }
  .disc__hub { width: 46px; height: 46px; border-radius: 50%; background: var(--charcoal-soft); border: 8px solid #5a5a5a; }

  /* Envelopes */
  .envelope {
    position: absolute; width: 520px; height: 290px; background: var(--charcoal); overflow: hidden;
  }
  .envelope--front { left: 60px; top: 560px; }
  .envelope--back { left: 620px; top: 560px; }
  .envelope__band {
    position: absolute; left: 0; top: 0; width: 100%; height: 76px; background: var(--orange);
    color: var(--paper); font-size: 14px; display: flex; align-items: center; justify-content: center;
  }
  .envelope__corner { position: absolute; left: 22px; top: 96px; width: 14px; height: 14px; background: var(--paper); }
  .envelope__contact {
    position: absolute; right: 24px; bottom: 20px; text-align: right;
    color: var(--paper); font-size: 9px; line-height: 1.65;
  }
  .envelope__flap {
    position: absolute; left: 0; top: 0; width: 100%; height: 110px; background: var(--orange);
    border-radius: 0 0 18px 18px;
  }
</style>
</head>
<body>

  <section class="folder">
    <div class="folder__band"><span class="logotype">Velvet Harbor</span></div>
    <div class="folder__watermark logotype">Velvet Harbor</div>
  </section>

  <section class="letterhead">
    <div class="letterhead__logo logotype">Velvet Harbor</div>
    <div class="letterhead__body">
      <p>Dear Partner, thank you for your continued interest in our franchise network. We are pleased to share the next steps for opening new locations across the region this year.</p>
      <p>Our team will guide each owner through site selection, staff training and supply planning so every restaurant opens on time and meets our shared standard of quality.</p>
      <p>Please contact our office with any questions. We look forward to working together.</p>
    </div>
    <div class="letterhead__foot"></div>
  </section>

  <section class="card card--front">
    <div class="card__band"><span class="logotype">Velvet Harbor</span></div>
    <div class="card__details">
      <div class="card__name">Omar Haddad</div>
      <div>Franchise Director</div>
      <div>+971 4 555 0142</div>
      <div>info@velvetharbor.com</div>
    </div>
  </section>

  <section class="card card--back">
    <span class="card__mark logotype">Velvet Harbor</span>
  </section>

  <section class="disc"><div class="disc__hub"></div></section>

  <section class="envelope envelope--front">
    <div class="envelope__band"><span class="logotype">Velvet Harbor</span></div>
    <div class="envelope__corner"></div>
    <address class="envelope__contact" style="font-style: normal;">
      Office: +971 4 555 0142<br>
      Mobile: +971 50 555 0187<br>
      Email: info@velvetharbor.com<br>
      P.O. Box: 2210, Dubai, UAE<br>
      www.velvetharbor.com
    </address>
  </section>

  <section class="envelope envelope--back">
    <div class="envelope__flap"></div>
  </section>

</body>
</html>
```